Redesign website for small print company

Vindurgata is a small printing company in Iceland mainly servicing Students, schools, etc. We are also doing all kind of other jobs, like business cards, book printing, brochure printing etc. We are also selling books online.
Our website is: www.vindurgata.is
What we are looking for is:
- Web Design (Uncoded - PSD layout only)
- Mobile friendly design, using our current color scheme: Red, green, yellow and light gray.
- Clean simple design
- Simple, light and easy to use.
- More menu Items/drop down
Industry/Entity Type
Digital Printing
Number of Pages Required
5+ page
Requirements
Must have
- Easy navigation
- Designed for mobile
- Current color scheme (see logo)
Nice to have
- Icon based products

```html
<!DOCTYPE html>
<html lang="en">
<head>
<meta charset="utf-8">
<title>Vindurgata – Printing</title>
<link href="https://fonts.googleapis.com/css2?family=Poppins:wght@400;500;600;700;800&display=swap" rel="stylesheet">
<style>
:root{
  --red:#e3262b;
  --red-deep:#c91e22;
  --green:#1b5e2a;
  --green-dark:#154a21;
  --yellow:#f5c400;
  --gray:#eeeeee;
  --ink:#222;
  --muted:#555;
  --white:#fff;
}
*{margin:0;padding:0;box-sizing:border-box}
html,body{width:1200px;height:3956px;overflow:hidden}
body{font-family:'Poppins',sans-serif;color:var(--ink);position:relative;background:var(--white)}
section,header,footer{position:absolute;left:0;width:1200px}
.abs{position:absolute}
.center{text-align:center}

/* hero */
.hero{top:0;height:717px;background:linear-gradient(180deg,#3b4046 0%,#585e63 45%,#2e3236 100%);color:var(--white)}
.topbar{top:0;left:0;width:1200px;height:50px;font-size:13px;display:flex;align-items:center;padding:0 82px}
.topbar span{margin-right:40px}
.topbar .right{margin-left:auto;display:flex;gap:22px}
.topbar .right span{margin:0}
.wordmark{font-weight:800;letter-spacing:.5px;color:var(--white)}
.brand{top:66px;left:82px;font-size:30px}
.nav{top:78px;right:82px;display:flex;gap:34px;font-size:16px;align-items:center}
.nav .active{color:var(--red)}
.nav .ico{width:16px;height:16px;border:2px solid #fff;border-radius:50%}
.hero-title{top:262px;left:0;width:1200px;font-size:80px;font-weight:800;line-height:1}
.hero-sub{top:356px;left:300px;width:600px;font-size:22px;font-weight:600;line-height:46px}
.btn{background:var(--red);color:#fff;border-radius:30px;font-weight:600;display:flex;align-items:center;justify-content:center}
.hero-btn{top:459px;left:515px;width:170px;height:50px;font-size:18px}
.social-side{top:285px;left:46px;display:flex;flex-direction:column;gap:26px;align-items:center}
.social-side i{display:block;width:12px;height:12px;background:#fff;border-radius:2px}
.follow{top:540px;left:32px;transform:rotate(-90deg);font-size:13px;transform-origin:left top}
.dots{top:388px;right:46px;display:flex;flex-direction:column;gap:24px;align-items:center}
.dots i{width:12px;height:12px;border-radius:50%;background:#fff}
.dots i.on{width:26px;height:26px;border:3px solid #fff;background:transparent}

/* features */
.features{top:717px;height:377px}
.feature{top:70px;width:330px;text-align:center}
.feature .circle{width:74px;height:74px;border-radius:50%;background:var(--red);margin:0 auto;display:flex;align-items:center;justify-content:center}
.feature h3{margin-top:34px;color:var(--green);font-size:17px;font-weight:700}
.feature p{margin:18px auto 0;width:260px;font-size:13px;line-height:24px;color:var(--muted)}

/* products */
.products{top:1094px;height:520px;background:linear-gradient(180deg,var(--green) 0%,var(--green-dark) 100%);color:var(--white)}
.sec-title{font-size:36px;font-weight:700}
.products .sec-title{top:55px;width:1200px}
.products .lead{top:112px;left:160px;width:880px;font-size:15px;line-height:32px}
.card{top:198px;width:322px;height:256px;background:#fff;text-align:center;color:var(--ink)}
.card svg{margin-top:26px}
.card h4{color:var(--red);font-size:18px;font-weight:500;margin-top:16px}
.card p{font-size:12px;line-height:20px;color:var(--muted);width:230px;margin:8px auto 0}
.card .more{color:var(--yellow);font-size:13px;margin-top:6px}
.arrow{top:310px;width:30px;height:30px;border-radius:50%;background:#222;display:flex;align-items:center;justify-content:center}

/* welcome */
.welcome{top:1614px;height:400px}
.welcome .shade{top:120px;left:486px;width:228px;height:270px;background:linear-gradient(180deg,rgba(245,196,0,.12),rgba(227,38,43,.08))}
.welcome .sec-title{top:70px;width:1200px;color:var(--green)}
.welcome p{left:116px;width:968px;font-size:15px;line-height:31px;color:var(--ink)}

/* gallery */
.gallery{top:2014px;height:831px}
.gallery .sec-title{top:46px;width:1200px;color:var(--red)}
.tabs{top:150px;left:118px;display:flex;gap:22px}
.tab{background:var(--red);color:#fff;font-size:14px;font-weight:500;height:34px;padding:0 14px;display:flex;align-items:center}
.tab.on{background:var(--green)}
.shot{width:324px;height:256px;box-shadow:0 2px 8px rgba(0,0,0,.15)}

/* contact */
.contact{top:2845px;height:710px;background:linear-gradient(180deg,var(--red) 0%,var(--red-deep) 100%);color:#fff}
.contact .sec-title{top:42px;width:1200px}
.contact .lead{top:108px;left:250px;width:700px;font-size:16px;line-height:34px}
.contact .photo{top:185px;left:543px;width:575px;height:467px;background:linear-gradient(135deg,#8a8f95,#4c4f54 60%,#a34a45)}
.form{top:219px;left:82px;width:527px;height:398px;background:#fff;color:var(--ink);padding:32px 42px}
.form h3{color:var(--green);font-size:26px;font-weight:700;margin-bottom:18px}
.row{display:flex;gap:18px;margin-bottom:18px}
.field{flex:1;height:48px;border:1px solid #ddd;box-shadow:0 2px 4px rgba(0,0,0,.08);font-size:13px;color:#888;padding:14px 16px}
.field.msg{height:88px}
.submit{width:142px;height:44px;font-size:17px;margin-top:18px}

/* footer */
.footer{top:3555px;height:401px;background:linear-gradient(180deg,#2b2b2b,#1b1b1b);color:#fff}
.footer .wordmark{top:82px;left:0;width:1200px;text-align:center;font-size:62px;line-height:1.2}
.finfo{top:186px;width:1200px;display:flex;justify-content:center;gap:46px;font-size:15px}
.fsocial{top:240px;width:1200px;display:flex;justify-content:center;gap:16px}
.fsocial i{width:42px;height:42px;border-radius:50%;background:var(--green);display:block}
.flinks{top:310px;width:1200px;font-size:15px}
.copy{top:356px;width:1200px;font-size:14px;font-weight:500}
</style>
</head>
<body>

<header class="hero" role="img" aria-label="Print shop floor with stacked paper and printing machines">
  <div class="abs topbar">
    <span>☎ 555 0142</span><span>◷ Mon - Fri: 9-17</span><span>✉ vork@vindurgata.is</span>
    <div class="right"><span>login</span><span>Register</span><span>English ▾</span></div>
  </div>
  <div class="abs wordmark brand">VINDURGATA</div>
  <nav class="abs nav"><span class="active">Home</span><span>Services</span><span>Job submit</span><span>About us</span><span class="ico"></span><span>🛒</span></nav>
  <div class="abs social-side"><i></i><i></i><i></i><i></i></div>
  <div class="abs follow">Follow us</div>
  <h1 class="abs hero-title center">VINDURGATA</h1>
  <p class="abs hero-sub center">Sed ut perspiciatis unde omnis iste natus error sit voluptatem accusantium doloremque</p>
  <div class="abs btn hero-btn">Read More</div>
  <div class="abs dots"><i></i><i class="on"></i><i></i></div>
</header>

<section class="features">
  <div class="abs feature" style="left:98px">
    <div class="circle"><svg width="34" height="34" viewBox="0 0 24 24"><path d="M4 11h4v10H4zM9 20V11l4-8c2 0 2 2 1.5 4L14 10h5c1.5 0 2 1 2 2l-2 7c-.3 1-1 1-2 1z" fill="#fff"/></svg></div>
    <h3>QUALITY PRINTING</h3>
    <p>Neque porro quisquam qui dold lorem ipsum quia dolor sit amet consec tetur adipisci velit consec tet.</p>
  </div>
  <div class="abs feature" style="left:418px">
    <div class="circle"><svg width="36" height="36" viewBox="0 0 24 24" fill="none" stroke="#fff" stroke-width="2"><circle cx="12" cy="12" r="9"/><path d="M12 7v5l3 3"/></svg></div>
    <h3>TIMELY DELIVERY</h3>
    <p>Neque porro quisquam qui dold lorem ipsum quia dolor sit amet consec tetur adipisci velit consec tet.</p>
  </div>
  <div class="abs feature" style="left:780px">
    <div class="circle"><svg width="34" height="34" viewBox="0 0 24 24"><path d="M20 3C9 3 4 9 4 16c0 2 .5 3 1 4 1-5 5-9 9-11-4 3-6 6-7 11 9 1 13-7 13-17z" fill="#fff"/></svg></div>
    <h3>ECO-MINDED</h3>
    <p>Neque porro quisquam qui dold lorem ipsum quia dolor sit amet consec tetur adipisci velit consec tet.</p>
  </div>
</section>

<section class="products">
  <h2 class="abs sec-title center">PRODUCT LIST</h2>
  <p class="abs lead center">Sed ut perspiciatis unde omnis iste natus error sit voluptatem accusantium doloremque laudantium, totam rem aperiam, eaque ipsa quae ab illo inventore veritatis et quasi architecto beatae vitae dicta sunt explicabo.</p>
  <div class="abs arrow" style="left:54px"><svg width="10" height="10" viewBox="0 0 10 10"><path d="M7 1L3 5l4 4" stroke="#fff" stroke-width="2" fill="none"/></svg></div>
  <div class="abs arrow" style="left:1110px"><svg width="10" height="10" viewBox="0 0 10 10"><path d="M3 1l4 4-4 4" stroke="#fff" stroke-width="2" fill="none"/></svg></div>
  <div class="abs card" style="left:100px">
    <svg width="96" height="66" viewBox="0 0 96 66" fill="none" stroke="#e3262b" stroke-width="3"><rect x="2" y="2" width="92" height="62" rx="4"/><circle cx="26" cy="24" r="8"/><path d="M12 48c2-10 26-10 28 0zM52 20h30M52 32h30M52 44h30"/></svg>
    <h4>BUSINESS CARDS</h4>
    <p>At vero eos et accusamus et iusto odio dignissimos ducimus qui blanditiis</p>
    <div class="more">Read More</div>
  </div>
  <div class="abs card" style="left:435px">
    <svg width="66" height="66" viewBox="0 0 66 66" fill="none" stroke="#e3262b" stroke-width="3"><path d="M22 6l-16 10 6 12 8-4v36h26V24l8 4 6-12-16-10c-2 6-20 6-22 0z"/><path d="M26 34h14M26 42h14"/></svg>
    <h4>POSTERS</h4>
    <p>At vero eos et accusamus et iusto odio dignissimos ducimus qui blanditiis</p>
    <div class="more">Read More</div>
  </div>
  <div class="abs card" style="left:773px">
    <svg width="80" height="66" viewBox="0 0 80 66" fill="none" stroke="#e3262b" stroke-width="3"><path d="M4 10l24-6 24 6 24-6v52l-24 6-24-6-24 6z"/><path d="M28 4v52M52 10v52M10 22h12M10 32h12M34 24h12M34 34h12M58 22h12M58 32h12"/></svg>
    <h4>LEAFLETS</h4>
    <p>At vero eos et accusamus et iusto odio dignissimos ducimus qui blanditiis</p>
    <div class="more">Read More</div>
  </div>
</section>

<section class="welcome">
  <div class="abs shade"></div>
  <h2 class="abs sec-title center">WELCOME TO UNIVERSITY</h2>
  <p class="abs center" style="top:130px">University education is a company located in the campus, which has specialized in the service of school staff, as well as providing general public printing. Higher education publishes seminars and first-class textbooks for courses, prints theses for lesson, as well as working on an unprecedented number of smaller pieces for students, teachers and organizations.These include brochures, reports, questionnaires, business cards, books, OCR scanning and more.</p>
  <p class="abs center" style="top:288px">Higher education is a tailored print shop, Green Leaf is the official eco-label of the Nordic countries, which has created a foothold in this country and is known among consumers.</p>
</section>

<section class="gallery">
  <h2 class="abs sec-title center">GALLERY</h2>
  <div class="abs tabs">
    <div class="tab on">All Projects</div><div class="tab">Leaflets &amp; Flyers</div><div class="tab">Stationary</div><div class="tab">3d Products</div><div class="tab">Presentation</div><div class="tab">Brochure</div><div class="tab">Ecommerce</div>
  </div>
  <div class="abs shot" style="top:241px;left:100px;background:linear-gradient(135deg,#d8d8d8,#7a8fa6 50%,#c0402f)" role="img" aria-label="Fanned-out printed brochures and flyers"></div>
  <div class="abs shot" style="top:241px;left:438px;background:linear-gradient(135deg,#333,#c46b2f 50%,#e2c44a)" role="img" aria-label="Stack of colourful printed book covers"></div>
  <div class="abs shot" style="top:241px;left:773px;background:linear-gradient(135deg,#e8e8e8,#e0357a 50%,#c9b43a)" role="img" aria-label="Printed textbook cover with pink title band"></div>
  <div class="abs shot" style="top:510px;left:100px;background:linear-gradient(135deg,#f0f0f0,#d9d6cc 60%,#c8b76a)" role="img" aria-label="Presentation folders and certificates"></div>
  <div class="abs shot" style="top:510px;left:438px;background:linear-gradient(135deg,#555,#e6e6e6 50%,#bbb)" role="img" aria-label="Stack of printed business cards"></div>
  <div class="abs shot" style="top:510px;left:773px;background:linear-gradient(135deg,#e4e4e4,#f7f7f7 50%,#b5c8a5)" role="img" aria-label="Stacks of white paper with green arrow"></div>
</section>

<section class="contact">
  <h2 class="abs sec-title center">CONTACT US</h2>
  <p class="abs lead center">At vero eos et accusamus et iusto odio dignissimos ducimus qui blanditiis praesentium voluptatum deleniti atque corrupti quos dolores et</p>
  <div class="abs photo" role="img" aria-label="Two print technicians checking a printed sheet at the press"></div>
  <div class="abs form">
    <h3>GET IN TOUCH</h3>
    <div class="row"><div class="field">Name</div><div class="field">Email</div></div>
    <div class="row"><div class="field">Phone Number</div><div class="field">Subject</div></div>
    <div class="field msg">Message</div>
    <div class="btn submit">Submit</div>
  </div>
</section>

<footer class="footer">
  <div class="abs wordmark">VINDURGATA</div>
  <div class="abs finfo"><span>➤ 21 Elm Row Street Springfield</span><span>☎ Phone: +555 0142</span><span>✉ Email: vork@vindurgata.is</span></div>
  <div class="abs fsocial"><i></i><i></i><i></i><i></i><i></i></div>
  <div class="abs flinks center">Home &nbsp;|&nbsp; Our Services &nbsp;|&nbsp; Job Submit &nbsp;|&nbsp; About us</div>
  <div class="abs copy center">Copyright © 2018, All Rights Reserved.</div>
</footer>

</body>
</html>
```